Business Card for Vorla Parts Wholesale supplier

Hi There! I need a new business card for our company. We are specialized in selling Vorla parts, mostly we sell new LCD screens for Zelnar and Drelks. I would like to see that back in the design.

You can find the colors and logo's on our website: www.hartuvo.nl

Industry/Entity Type

Business

Contact Information for Business Card

My Details:
Tobias Lindqvist

Phone: 0031687203316
E-mail: Tobias@hartuvo.nl

Slogan: "Because Quality Matters"

Font styles to use
Sans Serif

Colors

Designer to choose colors to be used in the design.

Requirements
Must have
• A Black backside with the Hartuvo logo on it. The front side should be clean with only my contact details.
• But I'm also open for something really different or awesome!
Nice to have
• Remember that we are in the parts & repairing industry, So i'll be handing those business cards mainly to repair companies. Maybe you can do something with that thought :)

```html
<!DOCTYPE html>
<html lang="en">
<head>
<meta charset="utf-8">
<title>Hartuvo Business Card</title>
<link href="https://fonts.googleapis.com/css2?family=Open+Sans:wght@400;600;700;800&display=swap" rel="stylesheet">
<style>
  :root {
    --orange: #f07322;
    --black: #0b0b0b;
    --white: #ffffff;
    --stage: #3a3a3a;
    --text-dark: #1a1a1a;
  }
  * { margin: 0; padding: 0; box-sizing: border-box; }
  html, body {
    width: 1200px; height: 880px; overflow: hidden;
    background: var(--stage);
    font-family: "Open Sans", Arial, sans-serif;
  }
  .canvas { position: relative; width: 1200px; height: 880px; }
  .card {
    position: absolute; width: 620px; height: 354px;
    border-radius: 18px; overflow: hidden;
    box-shadow: 0 14px 30px rgba(0,0,0,.45);
  }
  .card--back { left: 200px; top: 56px; background: var(--black); }
  .card--front { left: 380px; top: 466px; background: var(--white); }

  .brand { position: absolute; display: flex; align-items: center; gap: 14px; }
  .brand__mark { width: 52px; height: 52px; background: var(--orange); border-radius: 6px; }
  .brand__name { font-weight: 800; font-size: 74px; line-height: 1; letter-spacing: -1px; }
  .card--back .brand { left: 142px; top: 112px; }
  .card--back .brand__name { color: var(--white); }
  .card--front .brand { left: 46px; top: 66px; }
  .card--front .brand__name { color: var(--text-dark); }

  .slogan { position: absolute; font-size: 15px; white-space: nowrap; }
  .card--back .slogan { left: 0; right: 0; top: 222px; text-align: center; color: var(--white); }
  .card--front .slogan { left: 150px; top: 300px; font-weight: 700; color: var(--text-dark); }

  .wave { position: absolute; inset: 0; width: 620px; height: 354px; }

  .contact { position: absolute; left: 150px; top: 196px; color: var(--text-dark); }
  .contact__name { color: var(--orange); font-weight: 700; font-size: 22px; margin-bottom: 6px; white-space: nowrap; }
  .contact__row { display: flex; align-items: center; gap: 8px; font-size: 17px; line-height: 1.35; white-space: nowrap; }
  .contact__icon { width: 18px; height: 18px; flex: none; }

  .website { position: absolute; right: 132px; top: 262px; font-size: 16px; color: var(--text-dark); white-space: nowrap; }
  .website__domain { color: var(--orange); }
</style>
</head>
<body>
<main class="canvas">
  <section class="card card--back" aria-label="Business card back">
    <div class="brand">
      <span class="brand__mark"></span>
      <span class="brand__name">hartuvo</span>
    </div>
    <p class="slogan">Because Quality Matters</p>
  </section>

  <section class="card card--front" aria-label="Business card front">
    <svg class="wave" viewBox="0 0 620 354" aria-hidden="true">
      <path fill="var(--black)" d="M468 0 H620 V354 H558 C530 300 528 220 512 150 C498 80 490 30 468 0 Z"/>
      <path fill="var(--white)" d="M486 0 H620 V354 H582 C552 300 548 220 532 150 C518 80 508 30 486 0 Z"/>
      <path fill="var(--orange)" d="M502 0 H620 V354 H604 C568 300 566 220 550 150 C536 80 526 30 502 0 Z"/>
    </svg>

    <div class="brand">
      <span class="brand__mark"></span>
      <span class="brand__name">hartuvo</span>
    </div>

    <div class="contact">
      <p class="contact__name">Tobias Lindqvist</p>
      <p class="contact__row">
        <svg class="contact__icon" viewBox="0 0 18 18" aria-hidden="true">
          <rect width="18" height="18" rx="3" fill="var(--orange)"/>
          <path fill="var(--white)" d="M5 4h2.5l1 3-1.5 1a7 7 0 0 0 3 3l1-1.5 3 1V13a1 1 0 0 1-1 1A9 9 0 0 1 4 5a1 1 0 0 1 1-1z"/>
        </svg>
        0031687203316
      </p>
      <p class="contact__row">
        <svg class="contact__icon" viewBox="0 0 18 18" aria-hidden="true">
          <rect width="18" height="18" rx="3" fill="var(--orange)"/>
          <rect x="3.5" y="5" width="11" height="8" fill="none" stroke="var(--white)" stroke-width="1.4"/>
          <path d="M3.5 5l5.5 4.5L14.5 5" fill="none" stroke="var(--white)" stroke-width="1.4"/>
        </svg>
        Tobias@hartuvo.nl
      </p>
    </div>

    <p class="slogan">Because Quality Matters</p>
    <p class="website">www.<span class="website__domain">hartuvo</span>.nl</p>
  </section>
</main>
</body>
</html>
```